Stationery Design Project

We need a stationery design for our Norwegian trucking company. We have existed for about 15 years and our 12 drivers uses relatively new vehicles to transport goods around in northern Norway. Long distance routes with fresh fish og food transport is our main operations.

We have already made alogo that's printed on our trucks. The logo and a picture of our trucks is attached. I think the logo i crappy, but since its already in use, changing it is not an option in this round. Still using a better colour scheme in the overall stationery and more interesting fonts is possible (altso in the logo).

Company details:
Name: Kjelvraket AS
Organisation nr 873 615 309
Post adress: 8642 Raudvik

I like minimalism and simplicity. I am avalibly for questions in normal GMT working hours either here or on mail: ivar@fjordlast.no

Reason: Hi. Im extending the deadline because I needed some time to find a vector file of our logo. Sorry for the inconvenience

Hi, and thanks for all your interest in the project. Some updates:

-          I have decided to commit to using one of the designs. Some designer will get the payment.

-          I have extended the deadline with 24 hours since I needed some time to find our firms vector logo (a slow Swedish man was holding me up)

-          We will not choose a design before the deadline. No need to rush.

-          We have received a lot of great design and think there is a need to specified the product we want to make:

o   Business Card for all our employers. I just need the design and will duplicate with the correct numbers and name myself. The information on should be: Logo, employer’s name, Phone number, email, website, Postal number and address. Use this as a template: logo, Leif Brattvoll, 47382066, Leif@fjordlast.no,, fjordlast.no, 8642 Raudvik. The order and placement of the information is your creative decision.

o   Stickers to put on the goods we travel. On the sticker the should be the following information: Logo, phone number, Tekst and link: Fraktæ av Kjelvraket. Ke du syns? Fjordlast.no/tilbakemelding (this means: Handled by Kjelvraket. What do you think Fjordlast.no/feedback -à the link will be a feedback form). The placement the information and size is your creative decision with some stings: we have been thinking of using Drukko for printing and see that a size about 6x6 cm, 8x5 or something like that. (with 3000 copies our budget is 200 punds). Any suggestions of other suppliers are welcome. Drukko price calculator http://www.drukkolabelhouse.co.uk/digital-litho-printing/printing-labels-tags/stickers/

o   Letterhead with logo, address, phone number and organizational number.

o   Envelopes with logo,address, phone number and organizational number.

Have a nice day.

 

 

• Using the blue colour in the logo and using a similar graphic approch.

```html
<!DOCTYPE html>
<html lang="no">
<head>
<meta charset="utf-8">
<title>Kjelvraket – business cards</title>
<link rel="stylesheet" href="https://fonts.googleapis.com/css2?family=Open+Sans:wght@400;700&display=swap">
<style>
  :root {
    --stage: #262627;
    --card-white: #ffffff;
    --card-dark: #1f1e1e;
    --brand-blue: #1d5dab;
    --brand-blue-deep: #113f82;
    --swoosh: #1a1a1a;
    --text-dark: #333333;
    --text-light: #cfcfcf;
  }
  * { box-sizing: border-box; margin: 0; padding: 0; }
  html, body { width: 1200px; height: 252px; overflow: hidden; }
  body { font-family: "Open Sans", Arial, sans-serif; }

  .stage {
    position: relative;
    width: 1200px;
    height: 252px;
    background: var(--stage);
  }
  .card {
    position: absolute;
    top: 21px;
    width: 360px;
    height: 210px;
    border-radius: 13px;
    overflow: hidden;
  }
  .card--front { left: 20px; background: var(--card-white); }
  .card--back-light { left: 420px; background: var(--card-white); }
  .card--back-dark { left: 820px; background: var(--card-dark); }

  .card__wave { position: absolute; top: 0; left: 0; width: 360px; height: 96px; }

  .card__holder {
    position: absolute;
    top: 20px;
    right: 18px;
    color: #fff;
    font-size: 11px;
  }

  .brand {
    position: absolute;
    display: flex;
    align-items: center;
    gap: 7px;
    color: var(--brand-blue);
    font-weight: 700;
    font-size: 30px;
    letter-spacing: -0.5px;
  }
  .brand__dot {
    width: 12px; height: 12px;
    border-radius: 50%;
    background: var(--brand-blue);
  }
  .card--front .brand { left: 32px; top: 98px; }
  .card--back-light .brand,
  .card--back-dark .brand { left: 0; right: 0; justify-content: center; top: 82px; }
  .card--back-dark .brand { color: #1f5fb5; }
  .card--back-dark .brand__dot { background: #1f5fb5; }

  .card__address {
    position: absolute;
    left: 20px;
    bottom: 24px;
    font-size: 9px;
    line-height: 17px;
    color: var(--text-dark);
  }
  .card__contact {
    position: absolute;
    right: 18px;
    bottom: 24px;
    font-size: 9px;
    line-height: 17px;
    color: var(--text-dark);
    text-align: right;
  }
  .card__web {
    position: absolute;
    left: 0; right: 0;
    bottom: 22px;
    text-align: center;
    font-size: 8.5px;
    letter-spacing: 3px;
    color: var(--text-dark);
  }
  .card--back-dark .card__web { color: var(--text-light); }
</style>
</head>
<body>
<main class="stage" role="img" aria-label="Dark patterned presentation backdrop">

  <section class="card card--front">
    <svg class="card__wave" viewBox="0 0 360 96" aria-hidden="true">
      <defs>
        <linearGradient id="bandBlue" x1="0" y1="0" x2="0" y2="1">
          <stop offset="0" stop-color="#2a6fc0"/>
          <stop offset="1" stop-color="#113f82"/>
        </linearGradient>
      </defs>
      <path d="M0 0 H360 V52 C300 34 232 62 160 66 C92 70 42 52 0 58 Z" fill="url(#bandBlue)"/>
      <path d="M0 58 C42 52 92 70 160 66 C232 62 300 34 360 52 V62 C300 46 232 78 160 82 C92 86 42 68 0 74 Z" fill="#1a1a1a"/>
    </svg>
    <p class="card__holder">Leif Brattvoll</p>
    <div class="brand"><span class="brand__dot"></span>Kjelvraket</div>
    <p class="card__address">8642 Raudvik.<br>Organisation nr 873 615 309</p>
    <p class="card__contact">phone : 47382066<br>email : Leif@fjordlast.no<br>web : www.fjordlast.no</p>
  </section>

  <section class="card card--back-light">
    <div class="brand"><span class="brand__dot"></span>Kjelvraket</div>
    <p class="card__web">www.fjordlast.no</p>
  </section>

  <section class="card card--back-dark">
    <div class="brand"><span class="brand__dot"></span>Kjelvraket</div>
    <p class="card__web">www.fjordlast.no</p>
  </section>

</main>
</body>
</html>
```